Hearthstead Insurance Provider Website

We are selling Hearthstead Insurance policy / tenants Policy/Flood Insurance in USA in few states and planning expand nationally.

Our target audience are two folds: Customers (Buy policies) and Insurance Agents who wants to work with us to sell our policies to customers. But website should focus 80% on customers and 20% on agents. So, more customer focused user experience. Please note that there is no direct buy option for customers. They always go through insurance agents.

Customer focused, educational that makes buyer journey easy. We don’t want to come off as trying sell something as there is no direct sales involved from website.

Target Market(s)

Homeowners in USA and Insurance agent who sells these insurance.

Industry/Entity Type

Insurance

Number of Pages Required

4 page

Font styles to use
Other font styles liked:
• Open to suggestions

Colors

Designer to choose colors to be used in the design.

Requirements
Must have
• Three most important things: Trustworthy, Authentic, Simple
• Please use colors form logo and grays
• We like: www.hollowmere.com
• https://www.quillfenbrook.com/
• We need Agent Look up tool on home page similar to what is shown on example sites.
• Design:
• Home Page - Open to Ideas
• Insurance (Products) Landing Page - Info similar to: https://www.quillfenbrook.com/insurance/
• Agents Page - https://www.quillfenbrook.com/agents/
• Claims Page - Information similar to: https://www.quillfenbrook.com/claims-center/
• Site Navigation:
• Home
• Insurance
• Claims
• Agents
• About Us
• Contact Us
Nice to have
• Elegant, minimal and clean design that reflects trust and authenticity.
Should not have
• Slider or rotating images - prefer flat design. Not over powering design.

```html
<!DOCTYPE html>
<html lang="en">
<head>
<meta charset="utf-8">
<title>Hearthstead Insurance Co. — Home</title>
<link href="https://fonts.googleapis.com/css2?family=Source+Sans+3:wght@400;500;600;700&family=Outfit:wght@500&display=swap" rel="stylesheet">
<style>
:root{
  --navy:#1d3f8f;
  --navy-dark:#17316f;
  --red:#d31f2d;
  --ink:#2b2b2b;
  --text:#555;
  --muted:#6b6b6b;
  --hero-a:#f6f6f6;
  --hero-b:#dcdcdc;
  --footer:#f4f4f5;
  --white:#fff;
}
*{box-sizing:border-box;margin:0;padding:0}
html,body{width:942px;height:1200px;overflow:hidden;background:var(--white)}
body{position:relative;font-family:"Source Sans 3",sans-serif;color:var(--ink)}
a{color:inherit;text-decoration:none}
.abs{position:absolute}

/* header */
.site-header{position:absolute;left:0;top:0;width:942px;height:58px;background:var(--white)}
.brand{left:135px;top:12px;display:flex;align-items:center;gap:8px}
.brand-mark{width:26px;height:26px;border-radius:50%;background:var(--red)}
.brand-name{font-size:14px;font-weight:700;color:var(--navy);line-height:14px;letter-spacing:.4px}
.main-nav{left:348px;top:22px;display:flex;gap:14px;font-size:10.5px;font-weight:600;color:#333}
.main-nav .active{color:var(--red)}
.header-btn{top:16px;height:25px;color:var(--white);font-size:10.5px;font-weight:600;display:flex;align-items:center;justify-content:center;gap:4px;border-radius:2px}
.btn-careers{left:667px;width:68px;background:var(--navy)}
.btn-login{left:738px;width:69px;background:var(--red)}

/* hero */
.hero{left:0;top:58px;width:942px;height:354px;background:linear-gradient(90deg,var(--hero-a) 0%,#eeeeee 50%,var(--hero-b) 100%)}
.hero-photo{left:560px;top:58px;width:382px;height:354px;background:radial-gradient(ellipse at 55% 40%,#e9e3df 0%,#d9d6d4 55%,#cfcfcf 100%)}
.hero-title{left:134px;top:136px;font-family:"Outfit",sans-serif;font-weight:500;font-size:21px;color:#1b1b1b}
.hero-lead{left:135px;top:168px;width:305px;font-size:11.5px;line-height:18px;color:#444}
.agent-search{left:135px;top:222px;width:235px;height:38px;background:var(--white);border:1px solid #d4d4d4;border-radius:2px}
.agent-search .zip{position:absolute;left:11px;top:12px;font-size:10px;color:#888}
.btn-find{position:absolute;left:121px;top:2px;width:110px;height:32px;background:var(--red);color:var(--white);font-size:11px;font-weight:600;display:flex;align-items:center;justify-content:center;gap:6px;border-radius:2px}

/* product band */
.claims-band{left:0;top:412px;width:942px;height:165px;background:var(--red)}
.product{width:140px;height:140px;border-radius:50%;background:var(--white);display:flex;align-items:center;justify-content:center;top:342px}
.product-inner{width:128px;height:128px;border-radius:50%;background:linear-gradient(180deg,var(--navy) 0%,var(--navy-dark) 100%);display:flex;flex-direction:column;align-items:center;justify-content:center;color:var(--white);font-size:10.5px;font-weight:600;text-align:center;line-height:13px;gap:8px;padding-top:6px}
.claims-text{left:135px;top:512px;width:528px;font-size:13.5px;font-weight:600;line-height:17px;color:var(--white)}
.btn-report{left:716px;top:518px;width:90px;height:26px;background:#f4f4f4;border-radius:2px;font-size:10px;font-weight:600;color:#333;display:flex;align-items:center;justify-content:center}

/* insights */
.insights-title{left:0;top:618px;width:942px;text-align:center;font-size:21px;font-weight:700;color:#2e2e2e}
.insights-sub{left:0;top:652px;width:942px;text-align:center;font-size:11px;color:#444}
.insights-sub a{color:var(--red);text-decoration:underline}
.card{top:689px;width:212px}
.card-media{width:212px;height:153px}
.card-title{margin-top:15px;font-size:13.5px;font-weight:500;line-height:14px;color:#222}
.card-body{margin-top:7px;font-size:8.5px;line-height:14px;color:var(--muted)}

/* footer */
.site-footer{left:0;top:968px;width:942px;height:232px;background:var(--footer);border-top:1px solid #e6e6e6}
.f-col{top:1002px}
.f-col h4{font-size:11px;font-weight:500;color:#333;margin-bottom:10px}
.f-col li{list-style:none;font-size:8.8px;line-height:15.3px;color:var(--muted)}
.f-phone{font-size:13px;color:#333;line-height:14px}
.f-mail{font-size:8.8px;color:var(--muted)}
.social{display:flex;gap:4px;margin-top:12px}
.social span{width:24px;height:24px;border-radius:50%;border:1.5px solid #555}
.btn-footer-find{margin-top:14px;width:111px;height:32px;background:var(--red);color:var(--white);font-size:11px;font-weight:600;display:flex;align-items:center;justify-content:center;gap:6px;border-radius:2px}
.legal{left:0;top:1136px;width:942px;text-align:center;font-size:8.8px;line-height:15.5px;color:var(--muted)}
</style>
</head>
<body>

<header class="site-header">
  <a class="brand abs" href="#"><span class="brand-mark"></span><span class="brand-name">HEARTHSTEAD<br>INSURANCE CO.</span></a>
  <nav class="main-nav abs">
    <a class="active" href="#">Home</a><a href="#">Insurance</a><a href="#">About Us</a><a href="#">Claims</a><a href="#">Agents</a><a href="#">Contact Us</a>
  </nav>
  <a class="header-btn btn-careers abs" href="#">
    <svg width="9" height="9" viewBox="0 0 10 10" fill="#fff"><circle cx="5" cy="3" r="2.4"/><path d="M0.5 10c0-3 2-4.3 4.5-4.3S9.5 7 9.5 10z"/></svg>Careers</a>
  <a class="header-btn btn-login abs" href="#">
    <svg width="8" height="10" viewBox="0 0 8 10" fill="none" stroke="#fff" stroke-width="1.4"><path d="M2 4.5V3a2 2 0 0 1 4 0v1.5"/><rect x="0.7" y="4.5" width="6.6" height="5" fill="#fff" stroke="none"/></svg>Login</a>
</header>

<section class="hero abs"></section>
<div class="hero-photo abs" role="img" aria-label="Photo of a smiling woman reading on a tablet in a bright office"></div>
<h1 class="hero-title abs">Find an Agent</h1>
<p class="hero-lead abs">Talk to one of our local independent agencies to get a quote, ask questions about coverage options &amp; more!</p>
<form class="agent-search abs">
  <span class="zip">ZIP Code</span>
  <span class="btn-find">
    <svg width="14" height="14" viewBox="0 0 14 14" fill="none" stroke="#fff" stroke-width="1.4"><circle cx="7.5" cy="6.5" r="5"/><path d="M4 10l-3 3"/><circle cx="7.5" cy="5.3" r="1.4"/><path d="M5.3 9c.5-1.2 1.2-1.7 2.2-1.7S9.2 7.8 9.7 9"/></svg>Find an Agent</span>
</form>

<section class="claims-band abs"></section>

<a class="product abs" style="left:143px" href="#"><span class="product-inner">
  <svg width="40" height="36" viewBox="0 0 40 36" fill="#fff"><path d="M20 2L2 18h5v16h9V24h8v10h9V18h5z"/></svg>Homeowners</span></a>
<a class="product abs" style="left:315px" href="#"><span class="product-inner">
  <svg width="36" height="38" viewBox="0 0 36 38" fill="#fff"><path d="M6 2h24v36H6z"/><g fill="#1d3f8f"><rect x="10" y="6" width="4" height="4"/><rect x="16" y="6" width="4" height="4"/><rect x="22" y="6" width="4" height="4"/><rect x="10" y="13" width="4" height="4"/><rect x="16" y="13" width="4" height="4"/><rect x="22" y="13" width="4" height="4"/><rect x="10" y="20" width="4" height="4"/><rect x="16" y="20" width="4" height="4"/><rect x="22" y="20" width="4" height="4"/><rect x="15" y="28" width="6" height="10"/></g></svg>Renters/Condo</span></a>
<a class="product abs" style="left:487px" href="#"><span class="product-inner">
  <svg width="50" height="38" viewBox="0 0 50 38" fill="#fff"><path d="M18 2L1 17h5v19h22V17h5z"/><rect x="11" y="21" width="10" height="8" fill="#1d3f8f"/><path d="M40 36c-6 0-9-4-8-9 1-4 4-5 4-10 3 2 5 5 5 8 1-2 2-3 2-5 3 3 4 6 4 9 0 4-3 7-7 7z"/></svg>Dwelling Fire</span></a>
<a class="product abs" style="left:660px" href="#"><span class="product-inner">
  <svg width="40" height="38" viewBox="0 0 40 38" fill="none" stroke="#fff" stroke-width="2"><path d="M20 28c-7-8-10-13-10-17a10 10 0 0 1 20 0c0 4-3 9-10 17z" fill="#fff" stroke="none"/><circle cx="20" cy="11" r="4" fill="#1d3f8f" stroke="none"/><path d="M11 26L3 36h34l-8-10"/></svg>Agent Locator<br>Tool</span></a>

<p class="claims-text abs">To make it easy and stress free as possible, we have quick online form for you to report a claim or you can call us at 1-866-555-0142</p>
<a class="btn-report abs" href="#">Report a Claim</a>

<h2 class="insights-title abs">Plain Insights<sup style="font-size:11px">®</sup> by Hearthstead Insurance Co.</h2>
<p class="insights-sub abs">Take advantage of what we’ve learned through the years in <a href="#">Plain Insights<sup style="font-size:7px">®</sup></a></p>

<article class="card abs" style="left:135px">
  <div class="card-media" role="img" aria-label="Photo of a businessman holding a glowing house symbol in open hands" style="background:radial-gradient(ellipse at 50% 45%,#2f6f86 0%,#1c3546 55%,#12212c 100%)"></div>
  <h3 class="card-title">DIY Home Safety Audit</h3>
  <p class="card-body">Proin condimentum fermentum nunc. Etiam pharetra, erat sed fermentum feugiat velit mauris egestas quam ut aliquam massa nisl quis neque.</p>
</article>
<article class="card abs" style="left:365px">
  <div class="card-media" role="img" aria-label="Photo of payment cards resting on banknotes" style="background:linear-gradient(135deg,#7d8183 0%,#a9aaa6 45%,#8a8274 75%,#6e7478 100%)"></div>
  <h3 class="card-title">Common Rental and Landlord Scams</h3>
  <p class="card-body">Proin condimentum fermentum nunc. Etiam pharetra, erat sed fermentum feugiat velit mauris egestas quam ut aliquam massa nisl quis neque.</p>
</article>
<article class="card abs" style="left:594px">
  <div class="card-media" role="img" aria-label="Photo of a water drop falling from a blue tap" style="background:linear-gradient(90deg,#bfe7fb 0%,#6cc2f0 50%,#1f8fdc 100%)"></div>
  <h3 class="card-title">How to Save Water at Home</h3>
  <p class="card-body">Proin condimentum fermentum nunc. Etiam pharetra, erat sed fermentum feugiat velit mauris egestas quam ut aliquam massa nisl quis neque.</p>
</article>

<footer class="site-footer abs"></footer>
<div class="f-col abs" style="left:135px">
  <h4>Contact Info</h4>
  <p class="f-phone">1800 555 0187</p>
  <p class="f-mail">info@hearthsteadinsurance.co</p>
  <div class="social"><span></span><span></span><span></span><span></span></div>
</div>
<div class="f-col abs" style="left:307px">
  <h4>Our Company</h4>
  <ul><li>Home</li><li>Insurance</li><li>About Us</li><li>Claims</li><li>Agents</li></ul>
</div>
<div class="f-col abs" style="left:422px">
  <h4>Login to Your Account</h4>
  <ul><li>Agents Login</li><li>Clients login</li></ul>
  <a class="btn-footer-find" href="#">
    <svg width="14" height="14" viewBox="0 0 14 14" fill="none" stroke="#fff" stroke-width="1.4"><circle cx="7.5" cy="6.5" r="5"/><path d="M4 10l-3 3"/><circle cx="7.5" cy="5.3" r="1.4"/><path d="M5.3 9c.5-1.2 1.2-1.7 2.2-1.7S9.2 7.8 9.7 9"/></svg>Find an Agent</a>
</div>
<div class="f-col abs" style="left:577px">
  <h4>Customer Support</h4>
  <ul><li>FAQs</li><li>Resources</li><li>Report a Claim</li><li>Find an Agent</li></ul>
</div>
<div class="f-col abs" style="left:709px">
  <h4>Connect With Us</h4>
  <ul><li>Support</li><li>Careers</li></ul>
</div>
<div class="legal abs">
  <p>Copyright ©2018 Hearthstead Insurance. All Rights Reserved</p>
  <p>Terms of Use &nbsp;-&nbsp; Privacy Policy &nbsp;-&nbsp; Sitemap</p>
</div>

</body>
</html>
```